Verdant Systems Business Card

want the back of card to be blue- with the logo in the center
front of card- info plus logo (info being mailing address, email address, and website address )
4 different names with titles to have on cards
1) Calvin Borsted - Owner
2) Naomi Trelvik- Customer Relationship Specialist
3) Felix Andrade- Vice President of Sales
4) Owen Markby- Chief Technology Officer

Target Market(s)

tech company in the government/probation office industry

Industry/Entity Type

Government Office

Contact Information for Business Card

1) Calvin Borsted - Owner

Colors
0355a3
ffffff

Requirements
Must have
• back side should be blue, with the logo placed in the center
• front side needs to include both the logo, as well as company info (info should include website address, email address, and mailing address)

```html
<!DOCTYPE html>
<html lang="en">
<head>
<meta charset="utf-8">
<title>Verdant Systems Business Card</title>
<link rel="stylesheet" href="https://fonts.googleapis.com/css2?family=EB+Garamond:wght@600&family=Barlow:wght@400;600&display=swap">
<style>
  :root {
    --brand-blue: #0355a3;
    --brand-blue-deep: #03498c;
    --paper: #ffffff;
    --ink-grey: #7d8088;
    --rule: #a9abb1;
    --silver: #e3e8ef;
    --backdrop: #e4e5e8;
  }
  * { margin: 0; padding: 0; box-sizing: border-box; }
  html, body { width: 1200px; height: 769px; overflow: hidden; }
  body {
    background: var(--backdrop);
    font-family: "Barlow", sans-serif;
    position: relative;
  }
  .card {
    position: absolute;
    top: 230px;
    width: 540px;
    height: 309px;
    box-shadow: 0 6px 18px rgba(0,0,0,0.18);
  }
  .card-front { left: 45px; background: var(--paper); border-bottom: 9px solid var(--brand-blue); }
  .card-back { left: 615px; background: var(--brand-blue); }

  .brand {
    display: flex;
    align-items: center;
    gap: 10px;
    font-family: "EB Garamond", serif;
    font-weight: 600;
    letter-spacing: 0.06em;
    text-transform: uppercase;
    white-space: nowrap;
  }
  .brand-dot { border-radius: 50%; flex: none; }

  .card-front .brand {
    position: absolute;
    right: 40px;
    top: 55px;
    font-size: 27px;
    color: var(--brand-blue);
  }
  .card-front .brand-dot { width: 14px; height: 14px; background: var(--brand-blue); }

  .divider {
    position: absolute;
    left: 38px;
    right: 38px;
    top: 138px;
    border-top: 1px solid var(--rule);
  }
  .website {
    position: absolute;
    right: 40px;
    top: 150px;
    font-size: 13px;
    font-weight: 600;
    color: var(--brand-blue);
  }
  .person { position: absolute; left: 40px; top: 156px; }
  .person-name {
    font-family: "EB Garamond", serif;
    font-weight: 600;
    font-size: 24px;
    color: var(--brand-blue);
    line-height: 1.1;
  }
  .person-title { font-size: 13px; color: var(--ink-grey); margin-top: 2px; }
  .contacts { list-style: none; margin-top: 8px; }
  .contacts li {
    display: flex;
    align-items: center;
    gap: 9px;
    font-size: 13px;
    color: var(--ink-grey);
    line-height: 18px;
    white-space: nowrap;
  }
  .contacts svg { width: 11px; height: 11px; fill: var(--brand-blue); flex: none; }

  .card-back .brand {
    position: absolute;
    left: 50%;
    top: 50%;
    transform: translate(-50%, -50%);
    font-size: 36px;
    color: var(--silver);
  }
  .card-back .brand-dot { width: 18px; height: 18px; background: var(--silver); }
</style>
</head>
<body>
  <section class="card card-front" aria-label="Business card front">
    <div class="brand"><span class="brand-dot"></span>Verdant Systems</div>
    <div class="divider"></div>
    <div class="website">www.verdantsystems.com</div>
    <div class="person">
      <div class="person-name">Calvin Borsted</div>
      <div class="person-title">Owner</div>
      <ul class="contacts">
        <li>
          <svg viewBox="0 0 24 24" aria-hidden="true"><path d="M6.6 10.8a15.1 15.1 0 0 0 6.6 6.6l2.2-2.2a1 1 0 0 1 1-.25 11.4 11.4 0 0 0 3.6.57 1 1 0 0 1 1 1V20a1 1 0 0 1-1 1A17 17 0 0 1 3 4a1 1 0 0 1 1-1h3.5a1 1 0 0 1 1 1c0 1.25.2 2.45.57 3.57a1 1 0 0 1-.25 1z"/></svg>
          555-214-3086
        </li>
        <li>
          <svg viewBox="0 0 24 24" aria-hidden="true"><path d="M7 1h10a2 2 0 0 1 2 2v18a2 2 0 0 1-2 2H7a2 2 0 0 1-2-2V3a2 2 0 0 1 2-2zm0 3v14h10V4z"/></svg>
          555-318-6742
        </li>
        <li>
          <svg viewBox="0 0 24 24" aria-hidden="true"><path d="M2 5h20v14H2zm2 2v.5l8 5 8-5V7z"/></svg>
          calvin@verdantsystems.com
        </li>
        <li>
          <svg viewBox="0 0 24 24" aria-hidden="true"><path d="M12 1a8 8 0 0 0-8 8c0 6 8 14 8 14s8-8 8-14a8 8 0 0 0-8-8zm0 11a3 3 0 1 1 0-6 3 3 0 0 1 0 6z"/></svg>
          418 Larkmoor Avenue, Suite 12, Fenwick, OH 43210
        </li>
      </ul>
    </div>
  </section>

  <section class="card card-back" aria-label="Business card back">
    <div class="brand"><span class="brand-dot"></span>Verdant Systems</div>
  </section>
</body>
</html>
```